Real Estate Website - Phase I

We are looking to re-design our company website completely.
This will be for a real estate company which focuses on multiple lines of business/customers, including

1) Buyers - Investors, Owner Occupants
2) Sellers - Short Sales, Limited Services/Flat Fee, and Corporate/REO clients (the last being our core current customer)
3) Other Services: Default Services, Institutional Property Management, Field and Inspection Services
4) Agent FAQ's, instructions, etc to tie into our web-based offer management systems

For a brief understanding of what we do - Please see www.tvbalp.com. Current site does not address all of our current services.

Website must be able to be edited/added onto over time. We are also looking at redirects so that certain pages/sections can be given unique domain names to drive core customers to.

We work both with normal agents and buyers and large scale financial institutions, therefore our focus must be specific to each unique group based on the applicable page(s).

We had an incorrect amount in this brief.  It has since been corrected.

Please re-review.

Industry/Entity Type

Real Estate

Requirements
Must have
• *Property Search/Display - By various criteria AND by map
*Property Management back end for putting in new properties
*MObile Version or Mobile Friendly
*Analytics
*Contact Management and Lead Capture functions, including ability to export or use from site for email marketing campaigns. Lead capture must be able to sort by various criteria to tailor campaigns, ability to send out auto notices to staff and those signing up, etc.
* Signup option w/ functions for viewing not yet on market properties (subscription). This needs to be able to let buyers set search criteria and be auto notified whenever a property was listed or adjusted that met their criteria.
* SEO Optimization
* Syndication options to allow ease of syndication
* FAQ's and assistance pages to agents working with us
* Blog, social media boxes
* Ability for buyers to submit initial offers direct
* Functions and pages specific to below, with ability to cross promote and track (inquiry forms, etc to the below)
*Dedicated or preferred lender(s)
* Preferred vendors, etc

```html
<!DOCTYPE html>
<html lang="en">
<head>
<meta charset="utf-8">
<title>Harbor Line REO</title>
<link href="https://fonts.googleapis.com/css2?family=Arimo:wght@400;700&display=swap" rel="stylesheet">
<style>
:root{
  --ink:#333;
  --muted:#777;
  --blue:#2a5db0;
  --navy:#2b3590;
  --gold-hi:#f6d37a;
  --gold-lo:#e2ac3a;
  --rust:#c2571e;
  --dark:#3a3a3a;
  --footer:#2f2f2f;
  --footer-deep:#232323;
  --footer-head:#e3c15a;
  --line:#e2e2e2;
}
*{box-sizing:border-box;margin:0;padding:0}
html,body{width:839px;height:1200px;overflow:hidden}
body{position:relative;font-family:"Arimo",Arial,sans-serif;color:var(--ink);background:#fff;font-size:9px}
.abs{position:absolute}
a{color:inherit;text-decoration:none}

/* header */
.topline{left:0;top:0;width:839px;height:4px;background:#3a3a3a}
.header{left:0;top:4px;width:839px;height:93px;background:linear-gradient(#fff,#ececec)}
.brand{left:62px;top:22px;display:flex;align-items:center;gap:6px}
.brand-mark{width:52px;height:58px;background:var(--navy)}
.brand-name{font-size:23px;font-weight:700;color:var(--navy);line-height:1.05;width:140px}
.topnav{left:495px;top:32px;font-size:9px;color:#666}
.topnav span{margin:0 5px;color:#aaa}
.search-box{left:658px;top:27px;width:118px;height:20px;background:#fff;border:1px solid #ccc;font-size:8px;color:#555;padding:5px 0 0 8px}
.search-box svg{position:absolute;right:6px;top:4px}
.callus{left:493px;top:62px;font-size:13px;color:#555}
.callus b{color:var(--navy)}
.add-btn{left:658px;top:54px;width:118px;height:27px;background:linear-gradient(#4a55b8,#29338f);color:#fff;font-size:10px;display:flex;align-items:center;justify-content:center;gap:6px;border:1px solid #1f2875}

/* nav */
.mainnav{left:0;top:97px;width:839px;height:36px;background:linear-gradient(var(--gold-hi),var(--gold-lo));border-bottom:1px solid #c99328;display:flex;padding-left:63px}
.mainnav a{height:36px;display:flex;align-items:center;justify-content:center;font-size:9.5px;color:#4a3a1a;border-right:1px solid #d4a23c}
.mainnav a.active{background:#e5a12d;color:#fff}

/* hero */
.hero{left:0;top:133px;width:839px;height:304px;background:var(--dark)}
.slider{left:62px;top:147px;width:482px;height:276px;background:#888;border:1px solid #999;padding:5px}
.slide-img{width:470px;height:266px;background:linear-gradient(160deg,#9cc0e6 0%,#d9d6cf 35%,#7a4a2e 70%,#4d4d3a 100%)}
.caption{left:68px;top:370px;width:470px;height:48px;background:rgba(30,30,30,.55);padding:6px 14px}
.caption h2{font-size:14.5px;font-weight:400;color:#f0d58a}
.caption p{font-size:9.5px;color:#fff;margin-top:3px}
.arrows{left:478px;top:381px;display:flex;gap:4px}
.arrows span{width:23px;height:23px;border-radius:50%;background:#eee;border:2px solid #bbb;display:flex;align-items:center;justify-content:center}
.search-panel{left:560px;top:147px;width:216px;height:276px;background:#fff;border:4px solid #ccc;border-radius:3px}
.search-tab{left:557px;top:160px;width:175px;height:32px;background:linear-gradient(#3c49c0,#1f2a9a);color:#fff;font-size:12px;display:flex;align-items:center;padding-left:47px}
.search-tab svg{position:absolute;left:17px;top:7px}
.field{left:576px;width:184px;height:27px;border:1px solid #ccc;background:#fff;font-size:8.5px;color:#444;padding:7px 9px}
.field .caret{position:absolute;right:9px;top:11px;width:0;height:0;border-left:5px solid transparent;border-right:5px solid transparent;border-top:6px solid #777}
.bed-label{left:586px;top:359px;font-size:8.5px;color:#444}
.submit{left:694px;top:387px;width:66px;height:24px;background:linear-gradient(#d8d8d8,#a5a5a5);color:#fff;font-size:12px;border-radius:3px;display:flex;align-items:center;justify-content:center;border:1px solid #999}

/* feature cards */
.card{top:457px;width:226px;height:163px;background:#fff;border:1px solid var(--line);box-shadow:0 6px 8px -6px rgba(0,0,0,.25)}
.card-img{position:absolute;left:4px;top:4px;width:217px;height:116px;border:1px solid #ccc}
.card-title{position:absolute;left:10px;top:132px;display:flex;align-items:center;gap:10px;font-size:15.5px;color:var(--rust)}
.card-title i{width:17px;height:17px;border-radius:50%;background:#eee;border:1px solid #bbb;display:flex;align-items:center;justify-content:center}
.divider{left:70px;top:641px;width:700px;height:1px;background:var(--line)}

/* blog */
.panel-title{font-size:15px;color:var(--blue)}
.blog-title{left:77px;top:670px}
.blog-under{left:77px;top:696px;width:72px;height:3px;background:var(--blue)}
.blog-rule{left:77px;top:698px;width:336px;height:1px;background:#eee}
.dots{left:349px;top:676px;display:flex;gap:8px}
.dots i{width:6px;height:6px;border-radius:50%;background:#aaa}
.dots i:first-child{background:var(--blue)}
.post-thumb{left:80px;width:90px;height:60px;border:1px solid #ddd;padding:2px;background:#fff}
.post-thumb div{width:100%;height:100%}
.post{left:182px;width:225px}
.post h3{font-size:9.5px;font-weight:400;color:var(--blue)}
.post p{font-size:8.5px;color:var(--muted);line-height:13px;margin-top:5px}
.post time{display:block;font-size:8.5px;color:#333;margin-top:5px}

/* properties */
.props-title{left:442px;top:670px}
.props-rule{left:428px;top:698px;width:335px;height:1px;background:#eee}
.props-nav{left:742px;top:671px;font-size:13px;color:#777;letter-spacing:2px}
.prop{width:98px}
.prop-img{width:98px;height:74px;border:1px solid #ccc;padding:2px;background:#fff}
.prop-img div{width:100%;height:100%}
.prop h4{font-size:9.5px;font-weight:400;color:var(--blue);margin-top:12px}
.prop p{font-size:9px;color:#888;margin-top:2px}

/* footer */
.footer{left:0;top:986px;width:839px;height:170px;background:var(--footer);border-top:2px solid #222}
.footer-bottom{left:0;top:1156px;width:839px;height:44px;background:var(--footer-deep);color:#aaa;font-size:8.5px;text-align:center;padding-top:21px}
.fcol-head{font-size:12px;color:var(--footer-head)}
.fdiv{top:1000px;width:1px;height:144px;background:#444}
.quick{left:64px;top:1030px;list-style:none}
.quick li{font-size:8.5px;color:#ddd;height:20.5px}
.quick li::before{content:"•";margin-right:5px}
.testi{left:184px;width:226px;font-size:8.5px;color:#ddd;line-height:13px}
.testi q{quotes:none}
.testi .qm{color:#888;font-size:13px;font-weight:700}
.testi .who{color:var(--footer-head);margin-top:3px;display:block}
.ffield{left:443px;width:159px;height:20px;background:#fff;border:1px solid #999;font-size:7.5px;color:#333;padding:5px 10px}
.fsubmit{left:552px;top:1091px;width:50px;height:21px;background:linear-gradient(#f3d37d,#d8a53a);color:#3a2c10;font-size:10px;font-weight:700;display:flex;align-items:center;justify-content:center;border-radius:2px}
.social{left:632px;display:flex;align-items:center;gap:14px;font-size:8.5px;color:#ddd}
.social i{width:19px;height:19px;background:#666;display:block}
.social b{font-weight:400;color:#7fa3e0;font-size:9.5px}
</style>
</head>
<body>

<div class="abs topline"></div>
<header class="abs header"></header>
<div class="abs brand">
  <div class="brand-mark"></div>
  <div class="brand-name">HARBOR LINE REO</div>
</div>
<nav class="abs topnav"><a>Home</a><span>|</span><a>About us</a><span>|</span><a>Contact us</a></nav>
<div class="abs search-box">Search
  <svg width="11" height="11" viewBox="0 0 11 11"><circle cx="4.5" cy="4.5" r="3.3" fill="none" stroke="#222" stroke-width="1.6"/><line x1="7" y1="7" x2="10.3" y2="10.3" stroke="#222" stroke-width="2"/></svg>
</div>
<div class="abs callus">Call us : <b>336 555 0148</b></div>
<a class="abs add-btn"><svg width="11" height="11" viewBox="0 0 11 11"><circle cx="5.5" cy="5.5" r="5.5" fill="#fff"/><path d="M5.5 2.5v6M2.5 5.5h6" stroke="#2b3590" stroke-width="1.6"/></svg>ADD A PROPERTY</a>

<nav class="abs mainnav">
  <a class="active" style="width:70px">HOME</a>
  <a style="width:80px">ABOUT US</a>
  <a style="width:100px">OUR LISTINGS</a>
  <a style="width:72px">BUYERS</a>
  <a style="width:96px">SHORT SALES</a>
  <a style="width:72px">AGENTS</a>
  <a style="width:121px">ASSET MANAGERS</a>
  <a style="width:102px">CONTACT US</a>
</nav>

<section class="abs hero"></section>
<div class="abs slider"><div class="slide-img" role="img" aria-label="Photo of a modern two-storey villa with wooden garage doors"></div></div>
<div class="abs caption"><h2>Coral Crest Villa For Rent Limassol</h2><p>Coral Crest Villa For Rent Limassol Cyprus.</p></div>
<div class="abs arrows">
  <span><svg width="8" height="10" viewBox="0 0 8 10"><path d="M6 1L2 5l4 4" fill="none" stroke="#333" stroke-width="2"/></svg></span>
  <span><svg width="8" height="10" viewBox="0 0 8 10"><path d="M2 1l4 4-4 4" fill="none" stroke="#333" stroke-width="2"/></svg></span>
</div>

<div class="abs search-panel"></div>
<div class="abs search-tab"><svg width="18" height="18" viewBox="0 0 18 18"><circle cx="7.5" cy="7.5" r="5.5" fill="#cfe0ff" stroke="#fff" stroke-width="1.5"/><line x1="11.5" y1="11.5" x2="16" y2="16" stroke="#fff" stroke-width="2.5"/></svg>SEARCH PROPERTY</div>
<div class="abs field" style="top:203px">Location<span class="caret"></span></div>
<div class="abs field" style="top:240px">Price Range<span class="caret"></span></div>
<div class="abs field" style="top:277px">Area (Sq.M.)<span class="caret"></span></div>
<div class="abs field" style="top:314px">Keyword (City, State, or Zip Code)</div>
<div class="abs bed-label">Bed rooms :</div>
<div class="abs field" style="top:351px;left:642px;width:118px;height:28px"><span class="caret"></span></div>
<div class="abs submit">SUBMIT</div>

<div class="abs card" style="left:68px">
  <div class="card-img" role="img" aria-label="Photo of a family standing in front of their house" style="background:linear-gradient(160deg,#b8d3ec,#a7876a 45%,#6f8f4d)"></div>
  <div class="card-title"><i><svg width="5" height="7"><path d="M0 0l5 3.5L0 7z" fill="#888"/></svg></i>BUYERS</div>
</div>
<div class="abs card" style="left:306px">
  <div class="card-img" role="img" aria-label="Photo of agents beside a sold sign" style="background:linear-gradient(160deg,#3f6fb0,#c7434a 50%,#6f9a4a)"></div>
  <div class="card-title"><i><svg width="5" height="7"><path d="M0 0l5 3.5L0 7z" fill="#888"/></svg></i>AGENTS</div>
</div>
<div class="abs card" style="left:545px">
  <div class="card-img" role="img" aria-label="Photo of an asset manager meeting clients on a sofa" style="background:linear-gradient(160deg,#c4b6a2,#e6d9c6 50%,#8c6a55)"></div>
  <div class="card-title"><i><svg width="5" height="7"><path d="M0 0l5 3.5L0 7z" fill="#888"/></svg></i>ASSET MANAGERS</div>
</div>
<div class="abs divider"></div>

<h2 class="abs panel-title blog-title">Latest Blog</h2>
<div class="abs blog-rule"></div>
<div class="abs blog-under"></div>
<svg class="abs" style="left:107px;top:698px" width="12" height="6"><path d="M0 0h12L6 6z" fill="#2a5db0"/></svg>
<div class="abs dots"><i></i><i></i><i></i><i></i></div>

<div class="abs post-thumb" style="top:729px"><div role="img" aria-label="Photo of a house with a for sale sign" style="background:linear-gradient(#a9c9ea,#c9a46a 50%,#5f8a3b)"></div></div>
<article class="abs post" style="top:728px"><h3>Aliquam pharetra elementum nunc.</h3><p>Vestibulum tincidunt mi eget quam suscipit aliquam. Sed porttitor arcu quis massa luctus commodo.</p><time>Mar-6-2013</time></article>
<div class="abs post-thumb" style="top:810px"><div role="img" aria-label="Photo of a villa with palm trees" style="background:linear-gradient(#5f97d6,#d7c8a4 55%,#4f7a3a)"></div></div>
<article class="abs post" style="top:809px"><h3>Aliquam pharetra elementum nunc.</h3><p>Vestibulum tincidunt mi eget quam suscipit aliquam. Sed porttitor arcu quis massa luctus commodo.</p><time>Mar-6-2013</time></article>
<div class="abs post-thumb" style="top:897px;border-color:#eee"><div role="img" aria-label="Illustration of a small house model held in a hand" style="background:linear-gradient(#fff,#e8cfa3 60%,#f4e5d5)"></div></div>
<article class="abs post" style="top:896px"><h3>Aliquam pharetra elementum nunc.</h3><p>Vestibulum tincidunt mi eget quam suscipit aliquam. Sed porttitor arcu quis massa luctus commodo.</p><time>Mar-6-2013</time></article>

<h2 class="abs panel-title props-title">Our Properties</h2>
<div class="abs props-rule"></div>
<div class="abs props-nav">&lsaquo;&rsaquo;</div>

<div class="abs prop" style="left:443px;top:726px"><div class="prop-img"><div role="img" aria-label="Photo of a house in snow" style="background:linear-gradient(#c9d6e6,#7f7a74 55%,#eef1f4)"></div></div><h4>Propert Name</h4><p>Place</p></div>
<div class="abs prop" style="left:553px;top:726px"><div class="prop-img"><div role="img" aria-label="Photo of a brick house with a new listing ribbon" style="background:linear-gradient(#b6c7d9,#7c5545 55%,#e3e6ea)"></div></div><h4>Propert Name</h4><p>Place</p></div>
<div class="abs prop" style="left:663px;top:726px"><div class="prop-img"><div role="img" aria-label="Photo of a stone house" style="background:linear-gradient(#c6d6e6,#8c6e55 50%,#6d5a48)"></div></div><h4>Propert Name</h4><p>Place</p></div>
<div class="abs prop" style="left:443px;top:854px"><div class="prop-img"><div role="img" aria-label="Photo of a red brick house with garage" style="background:linear-gradient(#b3c9dd,#934a37 50%,#d9d9d9)"></div></div><h4>Propert Name</h4><p>Place</p></div>
<div class="abs prop" style="left:553px;top:854px"><div class="prop-img"><div role="img" aria-label="Photo of a stone house entrance" style="background:linear-gradient(#a7b89a,#8d6e52 50%,#6b7a4a)"></div></div><h4>Propert Name</h4><p>Place</p></div>
<div class="abs prop" style="left:663px;top:854px"><div class="prop-img"><div role="img" aria-label="Photo of a two-storey brick house" style="background:linear-gradient(#c3d5e8,#9a6a4f 55%,#8f8a7c)"></div></div><h4>Propert Name</h4><p>Place</p></div>

<footer class="abs footer"></footer>
<div class="abs fdiv" style="left:166px"></div>
<div class="abs fdiv" style="left:428px"></div>
<div class="abs fdiv" style="left:616px"></div>

<h3 class="abs fcol-head" style="left:64px;top:1001px;font-weight:400">Quick Links</h3>
<ul class="abs quick">
  <li>Integer lobortis</li><li>Curabitur ac</li><li>Phasellus tellus nisl</li><li>Aenean fringilla</li><li>Vestibulum</li><li>Aliquam commodo</li>
</ul>

<h3 class="abs fcol-head" style="left:184px;top:1001px;font-weight:400">Testimonials</h3>
<blockquote class="abs testi" style="top:1026px"><span class="qm">&ldquo;</span> Aliquam commo, mauris quis condimentum vehicula, ligula neque consequat diam, ac condimentum mauris felis a sem. Suspendisse vel orci esta. <span class="qm">&rdquo;</span><span class="who">Client Name, City</span></blockquote>
<blockquote class="abs testi" style="top:1097px"><span class="qm">&ldquo;</span> Aliquam commo, mauris quis condimentum vehicula, ligula neque consequat diam, condimentum. <span class="qm">&rdquo;</span><span class="who">Client Name, City</span></blockquote>

<h3 class="abs fcol-head" style="left:443px;top:1001px;font-weight:400">Email Signup</h3>
<div class="abs ffield" style="top:1031px">Name</div>
<div class="abs ffield" style="top:1061px">Email ID</div>
<div class="abs fsubmit">SUBMIT</div>

<h3 class="abs fcol-head" style="left:632px;top:1001px;font-weight:400">Connect with us</h3>
<div class="abs social" style="top:1031px"><i></i><span>Join with us on <b>Circlebook</b></span></div>
<div class="abs social" style="top:1060px"><i></i><span>Follow us on <b>Chirper</b></span></div>
<div class="abs social" style="top:1089px"><i></i><span>Share on <b>Linkline</b></span></div>
<div class="abs social" style="top:1118px"><i></i><span>Watch on <b>ViewTube</b></span></div>

<div class="abs footer-bottom">Copyright &copy; 2013 &nbsp;www.harborlinereo.com &nbsp;All rights reserved.</div>

</body>
</html>
```